Updated DJ business Card showing other businesses

DJ Talbo offers professional mobile dj services including DJ. MC. Karaoke.
Hush Party (will attach logo)
I also offer a 360 Photo Booth.

Contact info:
(405) 555-0147
mark.fenstell@pelimail.com
Social Media @DJTalboOKC

```html
<!DOCTYPE html>
<html lang="en">
<head>
<meta charset="utf-8">
<title>DJ Talbo Business Card</title>
<link href="https://fonts.googleapis.com/css2?family=Montserrat:wght@500;600&display=swap" rel="stylesheet">
<style>
  :root {
    --backdrop: #9a9a9a;
    --card-dark: #111111;
    --card-light: #ffffff;
    --ink: #111111;
    --ink-light: #f7f7f7;
    --accent: #d4204a;
  }
  * { margin: 0; padding: 0; box-sizing: border-box; }
  html, body { width: 1200px; height: 1000px; overflow: hidden; }
  body {
    background: var(--backdrop);
    font-family: "Montserrat", sans-serif;
    position: relative;
  }
  .card {
    position: absolute;
    left: 293px;
    width: 615px;
    height: 351px;
    border-radius: 30px;
    overflow: hidden;
  }
  .card-front { top: 144px; background: var(--card-dark); }
  .card-back { top: 540px; background: var(--card-light); color: var(--ink); }

  .brand-name {
    font-weight: 600;
    letter-spacing: 1px;
    white-space: nowrap;
  }
  .front-logo {
    position: absolute;
    left: 0; right: 0;
    top: 140px;
    text-align: center;
    font-size: 64px;
    line-height: 1;
    color: var(--ink-light);
    text-transform: uppercase;
  }

  .logo-row {
    position: absolute;
    top: 58px;
    left: 0; right: 0;
    display: flex;
    justify-content: center;
    align-items: center;
    gap: 40px;
  }
  .back-logo {
    font-size: 36px;
    color: var(--ink);
    text-transform: uppercase;
  }
  .partner-logo {
    display: flex;
    align-items: center;
    gap: 8px;
    font-size: 22px;
    color: var(--ink);
  }
  .partner-logo .mark {
    width: 30px; height: 30px;
    border-radius: 50%;
    background: var(--ink);
  }

  .services {
    position: absolute;
    top: 171px;
    left: 0; right: 0;
    text-align: center;
    font-size: 23px;
    font-weight: 500;
    letter-spacing: 0.3px;
  }

  .contact {
    position: absolute;
    left: 47px;
    top: 259px;
    font-size: 18px;
    font-weight: 500;
    line-height: 23px;
  }
  .contact-line { display: flex; align-items: center; gap: 6px; }
  .contact-line svg { width: 14px; height: 14px; fill: var(--accent); }

  .social {
    position: absolute;
    right: 58px;
    top: 258px;
    text-align: right;
    font-size: 18px;
    font-weight: 500;
  }
  .social-dots {
    display: flex;
    justify-content: flex-end;
    gap: 3px;
    margin: 0 22px 4px 0;
  }
  .social-dots span {
    width: 19px; height: 19px;
    border-radius: 50%;
    background: var(--accent);
  }
</style>
</head>
<body>
  <section class="card card-front">
    <div class="front-logo brand-name">DJ Talbo</div>
  </section>

  <section class="card card-back">
    <div class="logo-row">
      <div class="back-logo brand-name">DJ Talbo</div>
      <div class="partner-logo brand-name"><span class="mark"></span>Hush Party</div>
    </div>

    <p class="services">DJ, MC, Karaoke, 360 Photo Booth</p>

    <div class="contact">
      <div class="contact-line">
        <svg viewBox="0 0 24 24" aria-hidden="true"><path d="M6.6 10.8a15.1 15.1 0 0 0 6.6 6.6l2.2-2.2c.3-.3.7-.4 1-.2 1.1.4 2.3.6 3.6.6.6 0 1 .4 1 1V20c0 .6-.4 1-1 1A17 17 0 0 1 3 4c0-.6.4-1 1-1h3.5c.6 0 1 .4 1 1 0 1.3.2 2.5.6 3.6.1.3 0 .7-.2 1z"/></svg>
        <span>(405) 555-0147</span>
      </div>
      <div class="contact-line">
        <svg viewBox="0 0 24 24" aria-hidden="true"><path d="M2 5h20v14H2z M2 5l10 8 10-8" fill="var(--accent)"/><path d="M2 6l10 8 10-8" fill="none" stroke="#fff" stroke-width="1.6"/></svg>
        <span>mark.fenstell@pelimail.com</span>
      </div>
    </div>

    <div class="social">
      <div class="social-dots"><span></span><span></span><span></span><span></span></div>
      <div>@DJTalboOKC</div>
    </div>
  </section>
</body>
</html>
```